New Interrior Decoration company needs new website

We need a website for our new company specialising in interior decoration to residential and commercial markets.
We supply and install decorative and printed films for office and home decoration such as feature walls.
We would like to keep the design simple and clean.

Target Market(s)

Architects and interior designaers

Industry/Entity Type

It Company

Number of Pages Required

5+ page

Font styles to use
Sans Serif

Requirements
Must have
• Home page,
• Services/products page (split into commercial and residential)
• Gallery (split into commercial and residential)
• contact form and page
Nice to have
• Very clean and minimalistic design.

```html
<!DOCTYPE html>
<html lang="en">
<head>
<meta charset="utf-8">
<title>Halden Interiors</title>
<link href="https://fonts.googleapis.com/css2?family=Lato:ital,wght@0,400;0,700;1,700&family=Arimo:wght@400;700&display=swap" rel="stylesheet">
<style>
:root{
  --blue:#0b5cbf;
  --blue-band:#1667c9;
  --blue-deep:#07469a;
  --ink:#1b1b1b;
  --text:#555;
  --line:#c9c9c9;
  --white:#fff;
}
*{box-sizing:border-box;margin:0;padding:0}
html,body{width:1200px;height:3005px;overflow:hidden}
body{position:relative;background:var(--white);font-family:"Arimo",Arial,sans-serif;color:var(--text)}
.abs{position:absolute}
.heading{font-family:"Lato",sans-serif;font-weight:400;color:var(--ink);text-transform:uppercase}
.btn{position:absolute;background:var(--blue);color:var(--white);font-family:"Lato",sans-serif;font-size:20px;text-transform:uppercase;display:flex;align-items:center;justify-content:center;border-radius:4px}

/* header */
.top-rule{left:0;top:0;width:1200px;height:5px;background:var(--blue)}
.brand{left:78px;top:26px;display:flex;align-items:center;gap:14px}
.brand-square{width:62px;height:62px;background:var(--blue);border-radius:4px}
.brand-name{font-family:"Lato",sans-serif;font-weight:700;font-size:38px;line-height:1;color:#1e2a3a;text-transform:uppercase}
.top-email{left:634px;top:12px;font-size:15px;color:#444;display:flex;align-items:center;gap:10px}
.top-phone{left:918px;top:0;width:192px;height:38px;background:var(--blue);border-radius:0 0 8px 8px;color:var(--white);font-family:"Lato",sans-serif;font-size:20px;display:flex;align-items:center;justify-content:center;gap:12px}
.nav{left:540px;top:52px;display:flex;font-family:"Lato",sans-serif;font-size:17px;color:#222;text-transform:uppercase}
.nav a{height:44px;padding:0 22px;display:flex;align-items:center;color:inherit;text-decoration:none}
.nav a.active{background:var(--blue);color:var(--white);border-radius:3px}

/* hero */
.hero-photo{left:0;top:120px;width:1200px;height:562px;background:linear-gradient(100deg,#d9dcdf 0%,#eef0f1 40%,#c8c9ca 65%,#2a2a2c 72%,#4a4a4c 100%)}
.hero-title{left:0;top:328px;width:1200px;text-align:center;font-family:"Lato",sans-serif;font-style:italic;font-weight:700;font-size:40px;line-height:52px;color:var(--white);text-transform:uppercase;text-shadow:0 2px 6px rgba(0,0,0,.45)}
.hero-arrow{top:356px;width:50px;height:50px;border:2px solid rgba(255,255,255,.8);border-radius:50%;display:flex;align-items:center;justify-content:center}

/* about */
.about-title{left:78px;top:738px;font-size:42px}
.about-text{left:78px;top:800px;width:700px;font-size:15px;line-height:28px;color:#777}
.about-mark{left:854px;top:756px;width:268px;height:176px;display:flex;align-items:center;gap:16px}
.about-mark .sq{width:90px;height:90px;background:var(--blue);border-radius:6px;flex:none}
.about-mark .nm{font-family:"Lato",sans-serif;font-weight:700;font-size:28px;line-height:1.1;color:#1e2a3a;text-transform:uppercase}

/* services */
.service-band{left:0;top:1040px;width:1200px;height:422px;background:linear-gradient(120deg,#1a6cd0,#0d58b8 60%,#1565c8)}
.band-title{left:0;width:1200px;text-align:center;font-size:42px;color:#101a2a}
.band-lead{left:220px;width:760px;text-align:center;font-size:14px;line-height:24px;color:var(--white)}
.service-photo{top:1230px;width:248px;height:166px;border:2px solid #fff;box-shadow:0 6px 10px rgba(0,0,0,.3)}
.service-name{font-family:"Lato",sans-serif;font-size:19px;color:#0d1b2e;text-transform:uppercase}
.service-text{width:240px;font-size:14px;line-height:25px;color:var(--white)}
.read-more{font-family:"Lato",sans-serif;font-size:16px;color:var(--white);text-transform:uppercase;display:flex;align-items:center;gap:4px}

/* gallery */
.gallery-title{left:0;top:1522px;width:1200px;text-align:center;font-size:42px}
.tabs{left:0;top:1606px;width:1200px;display:flex;justify-content:center;gap:10px}
.tab{height:46px;padding:0 22px;border:2px solid #bdbdbd;font-family:"Lato",sans-serif;font-size:18px;color:#444;text-transform:uppercase;display:flex;align-items:center}
.tab.active{background:var(--blue);border-color:var(--blue);color:var(--white);padding:0 28px;border-radius:3px}
.tile{width:250px;height:178px}
.tile-feature{background:var(--blue);display:flex;flex-direction:column;align-items:center;justify-content:center;color:var(--white);font-family:"Lato",sans-serif}

/* contact */
.contact-band{left:0;top:2186px;width:1200px;height:260px;background:linear-gradient(120deg,#1a6cd0,#0d58b8 60%,#1565c8)}
.contact-panel{left:168px;top:2368px;width:864px;height:320px;background:var(--white);border-radius:6px}
.field{height:52px;border:1px solid var(--line);font-size:13px;color:#888;padding:0 14px;display:flex;align-items:center}

/* footer */
.footer{left:0;top:2700px;width:1200px;height:240px;background:var(--blue)}
.footer-bar{left:0;top:2940px;width:1200px;height:65px;background:var(--blue-deep);color:var(--white);font-size:15px;display:flex;align-items:center;justify-content:center}
.foot-head{font-family:"Lato",sans-serif;font-weight:700;font-size:16px;color:#0b1d35;text-transform:uppercase}
.foot-links{list-style:none;font-size:14px;color:var(--white);line-height:27px}
.foot-links li::before{content:"";display:inline-block;width:6px;height:6px;background:#0b1d35;margin:0 14px 2px 0}
.foot-text{font-size:14px;line-height:24px;color:var(--white)}
.social{width:38px;height:38px;background:#1b2c45;border:1px solid #6a88b6}
</style>
</head>
<body>

<!-- header -->
<div class="abs top-rule"></div>
<div class="abs brand"><div class="brand-square"></div><div class="brand-name">Halden<br>Interiors</div></div>
<div class="abs top-email">
  <svg width="18" height="13" viewBox="0 0 18 13"><rect width="18" height="13" rx="1" fill="#0b5cbf"/><path d="M1 1l8 6 8-6" stroke="#fff" stroke-width="1.6" fill="none"/></svg>
  info@haldeninteriors.com
</div>
<div class="abs top-phone">
  <svg width="18" height="18" viewBox="0 0 24 24"><path fill="#fff" d="M6.6 10.8a15 15 0 006.6 6.6l2.2-2.2a1 1 0 011-.25 11.4 11.4 0 003.6.57 1 1 0 011 1V20a1 1 0 01-1 1A17 17 0 013 4a1 1 0 011-1h3.5a1 1 0 011 1c0 1.250.2 2.45.57 3.57a1 1 0 01-.25 1z"/></svg>
  0 400 555 018
</div>
<nav class="abs nav"><a class="active">Home</a><a>About Us</a><a>Services</a><a>Gallery</a><a>Contact</a></nav>

<!-- hero -->
<div class="abs hero-photo" role="img" aria-label="Photograph of a bright modern office reception with orange chairs and a glossy dark feature wall"></div>
<div class="abs hero-title">We are specialising in interior decoration for<br>residential &amp; commercial markets.</div>
<div class="btn" style="left:454px;top:450px;width:290px;height:62px">Contact Us Know</div>
<div class="abs hero-arrow" style="left:14px"><svg width="14" height="22" viewBox="0 0 14 22"><path d="M11 2L3 11l8 9" stroke="#fff" stroke-width="2.5" fill="none"/></svg></div>
<div class="abs hero-arrow" style="left:1136px"><svg width="14" height="22" viewBox="0 0 14 22"><path d="M3 2l8 9-8 9" stroke="#fff" stroke-width="2.5" fill="none"/></svg></div>

<!-- about -->
<h2 class="abs heading about-title">About Halden Interiors</h2>
<p class="abs about-text">Lorem Ipsum is simply dummy text of the printing and typesetting industry. Lorem Ipsum has been the industry's standard dummy text ever since the 1500s, when an unknown printer took a galley of type and scrambled it to make but also the leap into electronic typesetting industry. when an un known printer took a galley of type..</p>
<div class="btn" style="left:78px;top:918px;width:186px;height:62px">Know More</div>
<div class="abs about-mark"><div class="sq"></div><div class="nm">Halden<br>Interiors</div></div>

<!-- services -->
<div class="abs service-band" role="img" aria-label="Blue-tinted photograph of an interior wall behind the services section"></div>
<h2 class="abs heading band-title" style="top:1098px">Our Service</h2>
<p class="abs band-lead" style="top:1158px">orem Ipsum is simply dummy text of the printing and typesetting industry. Lorem Ipsum has been the industry's standard dummy text ever since the 1500s, when</p>
<div class="abs service-photo" style="left:78px;background:linear-gradient(135deg,#e8e4dc,#b7a48a 60%,#6e5e4c)" role="img" aria-label="Photograph of a commercial reception with a curved wooden counter"></div>
<div class="abs service-name" style="left:344px;top:1234px">Commercial Design</div>
<p class="abs service-text" style="left:344px;top:1264px">Lorem Ipsum is simply dummy text of the printing and typesetting industry. Lorem Ipsum has been the industry's standard..</p>
<div class="abs read-more" style="left:344px;top:1372px">Read More... <svg width="14" height="12" viewBox="0 0 14 12"><path d="M1 1l5 5-5 5M7 1l5 5-5 5" stroke="#fff" stroke-width="2" fill="none"/></svg></div>
<div class="abs service-photo" style="left:608px;background:linear-gradient(135deg,#f3f3ea,#d9e07a 55%,#a7b94a)" role="img" aria-label="Photograph of a residential living room with a yellow-green printed feature wall"></div>
<div class="abs service-name" style="left:872px;top:1230px">Residential Design</div>
<p class="abs service-text" style="left:872px;top:1262px">Lorem Ipsum is simply dummy text of the printing and typesetting industry. Lorem Ipsum has been the industry's standard..</p>
<div class="abs read-more" style="left:872px;top:1370px">Read More... <svg width="14" height="12" viewBox="0 0 14 12"><path d="M1 1l5 5-5 5M7 1l5 5-5 5" stroke="#fff" stroke-width="2" fill="none"/></svg></div>

<!-- gallery -->
<h2 class="abs heading gallery-title">Our Gallery</h2>
<div class="abs tabs"><div class="tab active">All</div><div class="tab">Commercial Design</div><div class="tab">Residential Design</div></div>

<div class="abs tile tile-feature" style="left:78px;top:1676px"><div style="font-size:22px;text-transform:uppercase">Dream House</div><div style="font-size:16px;margin-top:4px">Residential</div></div>
<div class="abs tile" style="left:344px;top:1676px;background:linear-gradient(135deg,#d8c29a,#b58a5a 55%,#c0392b)" role="img" aria-label="Photograph of a room with a multicolour wood-plank feature wall and red chairs"></div>
<div class="abs tile" style="left:608px;top:1676px;background:linear-gradient(135deg,#cfcfd3,#8a8c93 60%,#a4312e)" role="img" aria-label="Photograph of a grey wall decorated with large curved and circle graphics"></div>
<div class="abs tile" style="left:872px;top:1676px;background:linear-gradient(135deg,#f3f3ea,#d9e07a 55%,#a7b94a)" role="img" aria-label="Photograph of a living room with a yellow-green patterned wall"></div>
<div class="abs tile" style="left:78px;top:1868px;background:linear-gradient(135deg,#c9a07a,#4aa3a0 55%,#2c6e6d)" role="img" aria-label="Photograph of a frosted glass partition with a teal dot pattern"></div>
<div class="abs tile" style="left:344px;top:1868px;background:linear-gradient(135deg,#e9eaea,#8d9093 55%,#2f3133)" role="img" aria-label="Photograph of a grey kitchen interior with pendant lights"></div>
<div class="abs tile" style="left:608px;top:1868px;background:linear-gradient(135deg,#f2e6c9,#d9a441 55%,#8a6a3c)" role="img" aria-label="Photograph of a shop interior with warm yellow shelving"></div>
<div class="abs tile" style="left:872px;top:1868px;background:linear-gradient(135deg,#7a3046,#5b2436 60%,#d9cfc6)" role="img" aria-label="Photograph of a lounge with a plum textured wall and white sofas"></div>
<div class="btn" style="left:506px;top:2062px;width:188px;height:62px">View All</div>

<!-- contact -->
<div class="abs contact-band" role="img" aria-label="Blue-tinted photograph of a brick wall and shelving behind the contact section"></div>
<h2 class="abs heading band-title" style="top:2244px">Contact Us</h2>
<p class="abs band-lead" style="top:2302px">Lorem Ipsum is simply dummy text of the printing and typesetting industry. Lorem Ipsum has been the industry's standard g and typesetting industry has been the industry's standard</p>
<div class="abs contact-panel"></div>
<div class="abs field" style="left:200px;top:2392px;width:260px">Name *</div>
<div class="abs field" style="left:470px;top:2392px;width:260px">Email *</div>
<div class="abs field" style="left:740px;top:2392px;width:258px">Contact No. *</div>
<div class="abs field" style="left:200px;top:2454px;width:798px;height:112px;align-items:flex-start;padding-top:14px">Message *</div>
<div class="btn" style="left:516px;top:2576px;width:166px;height:62px">Submit</div>

<!-- footer -->
<footer class="abs footer"></footer>
<div class="abs foot-head" style="left:78px;top:2730px">Usefull Links</div>
<ul class="abs foot-links" style="left:78px;top:2766px"><li>Home</li><li>About Us</li><li>Services</li><li>Gallery</li><li>Contact</li></ul>

<div class="abs foot-head" style="left:310px;top:2730px">Get In Touch</div>
<svg class="abs" style="left:310px;top:2774px" width="22" height="24" viewBox="0 0 22 24"><path fill="#0b1d35" d="M10 0h2v24h-2zM2 4h16l4 3-4 3H2zM4 12h16v6H4l-4-3z"/></svg>
<p class="abs foot-text" style="left:344px;top:2770px;width:240px">Lorem Ipsum is simple dummy text of printing and type srettin</p>
<svg class="abs" style="left:310px;top:2834px" width="20" height="14" viewBox="0 0 20 14"><rect width="20" height="14" rx="1" fill="#0b1d35"/><path d="M1 1l9 6 9-6" stroke="#5b8ad0" stroke-width="1.5" fill="none"/></svg>
<p class="abs foot-text" style="left:344px;top:2830px">info@haldeninteriors.com</p>
<svg class="abs" style="left:310px;top:2872px" width="20" height="20" viewBox="0 0 24 24"><path fill="#0b1d35" d="M6.6 10.8a15 15 0 006.6 6.6l2.2-2.2a1 1 0 011-.25 11.4 11.4 0 003.6.57 1 1 0 011 1V20a1 1 0 01-1 1A17 17 0 013 4a1 1 0 011-1h3.5a1 1 0 011 1c0 1.25.2 2.45.57 3.57a1 1 0 01-.25 1z"/></svg>
<p class="abs foot-text" style="left:344px;top:2870px">400 555 0182</p>

<div class="abs foot-head" style="left:598px;top:2730px">Newsletter</div>
<p class="abs foot-text" style="left:598px;top:2768px">Subscribe to the newsletter</p>
<div class="abs" style="left:592px;top:2806px;width:250px;height:46px;border:1px solid #cfe0f7;color:var(--white);font-size:14px;padding:0 14px;display:flex;align-items:center">Enter Your Email *</div>
<div class="abs" style="left:592px;top:2860px;width:250px;height:46px;background:var(--white);color:var(--blue);font-family:'Lato',sans-serif;font-size:18px;text-transform:uppercase;display:flex;align-items:center;justify-content:center;border-radius:3px">Subscribr</div>

<div class="abs" style="left:872px;top:2732px;display:flex;align-items:center;gap:10px">
  <div style="width:40px;height:40px;background:var(--white);border-radius:3px"></div>
  <div style="font-family:'Lato',sans-serif;font-weight:700;font-size:22px;line-height:1;color:var(--white);text-transform:uppercase">Halden<br>Interiors</div>
</div>
<div class="abs" style="left:900px;top:2804px;width:194px;height:1px;background:#7ea4d8"></div>
<div class="abs social" style="left:928px;top:2822px"></div>
<div class="abs social" style="left:978px;top:2822px"></div>
<div class="abs social" style="left:1028px;top:2822px"></div>

<div class="abs footer-bar">©HaldenInteriors - 2016. All rights reserved.</div>

</body>
</html>
```